Small Business Broker Business Card Design

A business card design for a small business brokerage, which is a financial service, not unlike real estate brokerage, but for small businesses such as laundromats, pizza shops, restaurants, cleaners etc. The designs should all be simple, more conservative in nature, using the colors and font of the logo. Again, think real estate Brokerage as a business context
Contact Information for Business Card
Name: Glen R. Harlow. Title: Small Business Advisor. Email: g.harlow@bayfieldcapitalworks.example. Mobile: (555) 274-3918. Office: (555) 806-2147. www.bayfieldcapitalworks.example

```html
<!DOCTYPE html>
<html lang="en">
<head>
<meta charset="UTF-8">
<title>Bayfield Capital Works – Business Card</title>
<link href="https://fonts.googleapis.com/css2?family=Montserrat:wght@400;500;700;800&display=swap" rel="stylesheet">
<style>
  :root {
    --navy: #1d3a6e;
    --green: #8cc63f;
    --white: #ffffff;
    --backdrop: #e6e8ec;
  }
  * { margin: 0; padding: 0; box-sizing: border-box; }
  html, body {
    width: 1200px; height: 800px; overflow: hidden;
    background: var(--backdrop);
    font-family: "Montserrat", sans-serif;
  }
  .canvas {
    width: 1200px; height: 800px;
    display: flex; flex-direction: column;
    align-items: center; justify-content: center; gap: 24px;
  }
  .card {
    width: 640px; height: 366px;
    border-radius: 22px; overflow: hidden; position: relative;
    box-shadow: 0 6px 18px rgba(0,0,0,.15);
  }
  /* front */
  .card--front {
    background: var(--navy);
    display: flex; align-items: center; justify-content: center;
  }
  .brand { text-align: center; }
  .brand__name {
    font-weight: 800; font-size: 30px; letter-spacing: 1px;
    text-transform: uppercase; color: var(--white);
    display: flex; align-items: center; justify-content: center; gap: 12px;
  }
  .brand__mark { width: 16px; height: 16px; background: var(--green); display: inline-block; }
  .brand__tagline {
    margin-top: 6px; font-weight: 700; font-size: 14px;
    letter-spacing: 1.6px; text-transform: uppercase; color: var(--green);
  }
  /* back */
  .card--back { background: var(--white); }
  .card__top {
    height: 212px; display: flex; align-items: center; justify-content: center;
  }
  .card--back .brand__name { color: var(--navy); }
  .card__band {
    position: absolute; left: 0; right: 0; bottom: 0; height: 154px;
    background: var(--navy); border-top: 3px solid var(--green);
    display: flex; align-items: center; padding: 0 36px;
  }
  .person { width: 250px; }
  .person__name { font-weight: 700; font-size: 28px; color: var(--green); }
  .person__title { margin-top: 4px; font-weight: 400; font-size: 15px; color: var(--white); }
  .divider { width: 1.5px; height: 96px; background: var(--green); margin: 0 22px; }
  .contacts { list-style: none; }
  .contacts li {
    display: flex; align-items: center; gap: 10px;
    font-size: 13px; color: var(--white); line-height: 24px;
  }
  .contacts svg { width: 14px; height: 14px; flex: none; }
</style>
</head>
<body>
<main class="canvas">
  <section class="card card--front">
    <div class="brand">
      <div class="brand__name"><span class="brand__mark"></span>Bayfield Capital Works, Inc</div>
      <div class="brand__tagline">Confidently buy or sell a local business today</div>
    </div>
  </section>

  <section class="card card--back">
    <div class="card__top">
      <div class="brand">
        <div class="brand__name"><span class="brand__mark"></span>Bayfield Capital Works, Inc</div>
        <div class="brand__tagline">Confidently buy or sell a local business today</div>
      </div>
    </div>
    <div class="card__band">
      <div class="person">
        <div class="person__name">Glen R. Harlow</div>
        <div class="person__title">Small Business Advisor</div>
      </div>
      <div class="divider"></div>
      <ul class="contacts">
        <li>
          <svg viewBox="0 0 16 16" aria-hidden="true"><rect x="1" y="6" width="14" height="8" rx="2" fill="#8cc63f"/><path d="M2 6c0-4 12-4 12 0" stroke="#8cc63f" stroke-width="2" fill="none"/></svg>
          (555) 806-2147
        </li>
        <li>
          <svg viewBox="0 0 16 16" aria-hidden="true"><rect x="4" y="1" width="8" height="14" rx="1.5" fill="#8cc63f"/><rect x="5.5" y="3" width="5" height="8" fill="#1d3a6e"/></svg>
          (555) 274-3918
        </li>
        <li>
          <svg viewBox="0 0 16 16" aria-hidden="true"><rect x="1" y="3" width="14" height="10" rx="1" fill="#8cc63f"/><path d="M1 4l7 5 7-5" stroke="#1d3a6e" stroke-width="1.4" fill="none"/></svg>
          g.harlow@bayfieldcapitalworks.example
        </li>
        <li>
          <svg viewBox="0 0 16 16" aria-hidden="true"><circle cx="8" cy="8" r="6.5" fill="none" stroke="#8cc63f" stroke-width="1.5"/><ellipse cx="8" cy="8" rx="3" ry="6.5" fill="none" stroke="#8cc63f" stroke-width="1.2"/><path d="M1.5 8h13" stroke="#8cc63f" stroke-width="1.2"/></svg>
          www.bayfieldcapitalworks.example
        </li>
      </ul>
    </div>
  </section>
</main>
</body>
</html>
```